Business Card Design Project

Actor, Producer, Vocal Coach, Choral Director, Song WriterPhone: (215) 555-0142 Fax: (215) 856-3933Email: waltierblocker@gmail.comFacebook: facebook.com/waltier.blockerTwitter: @thedf482

Industry/Entity Type

Business

Contact Information for Business Card

Business Cards that include my picture

Colors

Designer to choose colors to be used in the design.

```html
<!DOCTYPE html>
<html lang="en">
<head>
<meta charset="utf-8">
<title>Dorian Fellsmore — Business Card</title>
<link href="https://fonts.googleapis.com/css2?family=Montserrat:wght@300;400;700;800&display=swap" rel="stylesheet">
<style>
  :root {
    --stage: #e9e9ea;
    --card-white: #ffffff;
    --header-grey: #f1f1f1;
    --band-grey: #e4e4e2;
    --panel-grey: #dcdbd6;
    --mauve: #b9abaf;
    --mauve-deep: #a8989c;
    --ink: #111111;
    --ink-soft: #3a3a3a;
    --black-band: #1b1b1b;
  }
  * { box-sizing: border-box; margin: 0; padding: 0; }
  html, body {
    width: 1200px; height: 863px; overflow: hidden;
    background: var(--stage);
    font-family: 'Montserrat', sans-serif;
  }
  .card {
    position: absolute;
    top: 134px;
    width: 340px; height: 594px;
    overflow: hidden;
    box-shadow: 0 10px 30px rgba(0,0,0,0.12);
  }
  /* Front */
  .card--front { left: 230px; background: var(--card-white); }
  .front__pattern {
    position: absolute; left: 0; top: 0; width: 100%; height: 120px;
    background: var(--header-grey);
  }
  .front__band {
    position: absolute; left: 0; top: 120px; width: 100%; height: 105px;
    background: var(--band-grey);
  }
  .front__portrait {
    position: absolute; left: 83px; top: 52px;
    width: 174px; height: 174px; border-radius: 50%;
    background: radial-gradient(circle at 50% 40%, #f4f1f0 0%, #d9d2d2 60%, #b9abaf 100%);
    border: 6px solid var(--card-white);
    box-shadow: 0 6px 0 var(--mauve);
  }
  .front__identity {
    position: absolute; left: 0; top: 262px; width: 100%;
    text-align: center;
  }
  .front__name {
    font-weight: 800; font-size: 21px; letter-spacing: 0.5px;
    color: var(--ink); text-transform: uppercase;
  }
  .front__roles {
    margin-top: 6px;
    font-weight: 300; font-size: 14px; line-height: 17px;
    color: var(--ink-soft);
  }
  .front__contact {
    position: absolute; left: 24px; top: 400px;
    width: 292px; height: 128px;
    background: var(--panel-grey); border-radius: 10px;
  }
  .contact__icons {
    position: absolute; left: 0; top: -8px;
    width: 30px; height: 144px; border-radius: 15px;
    background: var(--ink);
    display: flex; flex-direction: column; align-items: center; justify-content: space-evenly;
    padding: 6px 0;
  }
  .contact__icon {
    width: 18px; height: 18px; border-radius: 50%;
    background: var(--card-white);
    display: flex; align-items: center; justify-content: center;
  }
  .contact__list {
    position: absolute; left: 42px; top: 6px;
    list-style: none;
    font-weight: 400; font-size: 14px; line-height: 23px;
    color: var(--ink);
  }
  .front__footer {
    position: absolute; left: 0; bottom: 0; width: 100%; height: 16px;
    background: var(--mauve);
  }
  /* Back */
  .card--back { left: 630px; background: var(--mauve); }
  .back__pattern {
    position: absolute; left: 0; top: 0; width: 100%; height: 420px;
    background: linear-gradient(180deg, var(--mauve) 0%, var(--mauve-deep) 100%);
  }
  .back__band {
    position: absolute; left: 0; bottom: 0; width: 100%; height: 150px;
    background: var(--black-band);
  }
  .back__badge {
    position: absolute; left: 85px; top: 340px;
    width: 170px; height: 170px; border-radius: 50%;
    background: var(--header-grey);
    display: flex; align-items: center; justify-content: center;
  }
  .back__initials {
    font-weight: 800; font-size: 64px; letter-spacing: -2px;
    color: var(--ink);
  }
</style>
</head>
<body>
  <section class="card card--front">
    <div class="front__pattern" role="img" aria-label="Faint pattern of film reels and music notes"></div>
    <div class="front__band"></div>
    <div class="front__portrait" role="img" aria-label="Portrait photo of Dorian Fellsmore"></div>
    <div class="front__identity">
      <h1 class="front__name">Dorian Fellsmore</h1>
      <p class="front__roles">Actor, Producer<br>Vocal Coach, Choral Director<br>Song Writer</p>
    </div>
    <div class="front__contact">
      <div class="contact__icons">
        <span class="contact__icon">
          <svg width="10" height="10" viewBox="0 0 24 24"><path fill="#111" d="M6.6 10.8a15 15 0 0 0 6.6 6.6l2.2-2.2a1 1 0 0 1 1-.25 11.4 11.4 0 0 0 3.6.57 1 1 0 0 1 1 1V20a1 1 0 0 1-1 1A17 17 0 0 1 3 4a1 1 0 0 1 1-1h3.5a1 1 0 0 1 1 1c0 1.25.2 2.45.57 3.57a1 1 0 0 1-.25 1z"/></svg>
        </span>
        <span class="contact__icon">
          <svg width="10" height="10" viewBox="0 0 24 24"><rect x="6" y="2" width="12" height="6" fill="#111"/><rect x="2" y="9" width="20" height="9" rx="2" fill="#111"/><rect x="6" y="15" width="12" height="7" fill="#111"/></svg>
        </span>
        <span class="contact__icon">
          <svg width="10" height="10" viewBox="0 0 24 24"><rect x="2" y="5" width="20" height="14" rx="2" fill="#111"/><path d="M3 6l9 7 9-7" stroke="#fff" stroke-width="2" fill="none"/></svg>
        </span>
        <span class="contact__icon"></span>
        <span class="contact__icon"></span>
      </div>
      <ul class="contact__list">
        <li>(215) 555-0142</li>
        <li>(215) 555-0187</li>
        <li>dorianfellsmore@postlane.net</li>
        <li>dorian.fellsmore</li>
        <li>@thedf482</li>
      </ul>
    </div>
    <div class="front__footer"></div>
  </section>

  <section class="card card--back">
    <div class="back__pattern" role="img" aria-label="Pattern of film reels and music notes"></div>
    <div class="back__band"></div>
    <div class="back__badge">
      <span class="back__initials">DF</span>
    </div>
  </section>
</body>
</html>
```